Business Card for Multi-Brand Sportswear Company

We are looking for a business card which represents our company and the multiple brands within it.

The company: Fen Athletics (LTD)
The brands: Fen, TavaPuni, ElmStretch, Grit and Rain

Employees using these cards would be representing Fen Athletics, rather than any of the individual brands. You will see a current design within the uploaded files, to give some inspiration. The actual text of the brands is not necessary, but the logos should be on there is some format.

Our creative minds on this are stretched, so we are looking for someone to make this their own, and show us what a good business card should look like.

We may like to get these printed with spot gloss, so keep that in mind with your designs.

www.fenathletics.co.uk

Industry/Entity Type

Business

Contact Information for Business Card

Leo Pemberton-Hale
Operations Manager
(+44) 1632 960 418
Leo@fenathletics.co.uk
www.fenathletics.co.uk

Font styles to use
Sans Serif
Other font styles liked:
• Eurostile

Colors
ffffff

Requirements
Nice to have
• Dark (black) background

```html
<!DOCTYPE html>
<html lang="en">
<head>
<meta charset="utf-8">
<title>Fen Athletics – Business Card</title>
<link href="https://fonts.googleapis.com/css2?family=Open+Sans:wght@400;600&family=Michroma&display=swap" rel="stylesheet">
<style>
  :root {
    --bg: #e9e7e4;
    --white: #ffffff;
    --black: #050505;
    --red: #e31b23;
    --grey: #9a9a9a;
    --light: #f2f2f2;
  }
  * { margin: 0; padding: 0; box-sizing: border-box; }
  html, body { width: 1200px; height: 900px; overflow: hidden; }
  body { background: var(--bg); position: relative; font-family: "Open Sans", Arial, sans-serif; }

  .card { position: absolute; overflow: hidden; box-shadow: 0 6px 18px rgba(0,0,0,.18); }
  .card-front { left: 78px; top: 33px; width: 588px; height: 365px; background: var(--white); }
  .card-back { left: 388px; top: 505px; width: 566px; height: 352px; background: var(--black); }

  .card-shapes { position: absolute; inset: 0; }

  .brand-lockup { position: absolute; text-align: left; }
  .brand-name { font-family: "Open Sans", Arial, sans-serif; font-weight: 600; text-transform: uppercase; letter-spacing: 1px; line-height: 1; }
  .brand-tagline { font-family: "Michroma", Arial, sans-serif; text-transform: uppercase; letter-spacing: 1.5px; margin-top: 6px; }

  .card-front .brand-lockup { left: 108px; top: 82px; }
  .card-front .brand-name { font-size: 38px; color: var(--black); }
  .card-front .brand-tagline { font-size: 9px; color: var(--black); text-align: right; }

  .holder { position: absolute; right: 316px; top: 252px; text-align: right; }
  .holder-name { color: var(--red); font-size: 18px; font-weight: 600; line-height: 1.2; }
  .holder-title { color: var(--white); font-size: 14px; line-height: 1.4; }

  .contact-list { position: absolute; left: 293px; top: 242px; list-style: none; }
  .contact-list li { display: flex; align-items: center; color: var(--white); font-size: 15px; height: 21px; }
  .contact-list svg { width: 12px; height: 12px; margin-right: 13px; fill: var(--red); flex: none; }

  .address { position: absolute; left: 158px; top: 312px; color: var(--grey); font-size: 14px; }

  .card-back .brand-lockup { left: 60px; top: 120px; }
  .card-back .brand-name { font-size: 40px; color: var(--red); }
  .card-back .brand-tagline { font-size: 9px; color: var(--red); text-align: right; }

  .brand-band {
    position: absolute; left: 0; top: 243px; width: 100%; height: 67px;
    background: linear-gradient(90deg, #e01b22 0%, #d81a20 55%, #7a0d10 82%, var(--black) 100%);
    display: flex; align-items: center;
  }
  .brand-band-item { position: absolute; font-size: 14px; font-weight: 600; color: var(--light); white-space: nowrap; transform: translateX(-50%); }
</style>
</head>
<body>

<section class="card card-front">
  <svg class="card-shapes" viewBox="0 0 588 365" aria-hidden="true">
    <polygon points="0,182 0,207 386,207 412,179 0,179" fill="var(--red)"/>
    <polygon points="0,212 388,212 416,172 588,172 588,365 0,365" fill="var(--black)"/>
  </svg>

  <div class="brand-lockup">
    <div class="brand-name">Fen Athletics</div>
    <div class="brand-tagline">Performance Wear</div>
  </div>

  <div class="holder">
    <div class="holder-name">Ned Harcastle</div>
    <div class="holder-title">Managing Director</div>
  </div>

  <ul class="contact-list">
    <li><svg viewBox="0 0 12 12"><path d="M2.5 0.5l2 2-1.2 1.6c.7 1.6 2 2.9 3.6 3.6L8.5 6.5l2 2-1.5 2.5C4.5 10.5 1 7 .5 3z"/></svg>+44(0)1632 960418</li>
    <li><svg viewBox="0 0 12 12"><path d="M1 2.5h10v7H1z M1 2.5l5 4 5-4" stroke="var(--black)" stroke-width=".8"/></svg>ned@fenathletics.co.uk</li>
    <li><svg viewBox="0 0 12 12"><circle cx="6" cy="6" r="5.5"/><path d="M.5 6h11M6 .5v11M2 3h8M2 9h8" stroke="var(--black)" stroke-width=".8" fill="none"/></svg>www.fenathletics.co.uk</li>
  </ul>

  <div class="address">Lower Green,Harwick, Fenby,YO9 4ZZ</div>
</section>

<section class="card card-back">
  <div class="brand-lockup">
    <div class="brand-name">Fen Athletics</div>
    <div class="brand-tagline">Performance Wear</div>
  </div>

  <div class="brand-band">
    <span class="brand-band-item" style="left:67px">TavaPuni</span>
    <span class="brand-band-item" style="left:212px">Fen</span>
    <span class="brand-band-item" style="left:374px">Grit and Rain</span>
    <span class="brand-band-item" style="left:488px">ElmStretch</span>
  </div>
</section>

</body>
</html>
```